Business Card for Multi-Brand Sportswear Company

We are looking for a business card which represents our company and the multiple brands within it.

The company: Fen Athletics (LTD)
The brands: Fen, TavaPuni, ElmStretch, Grit and Rain

Employees using these cards would be representing Fen Athletics, rather than any of the individual brands. You will see a current design within the uploaded files, to give some inspiration. The actual text of the brands is not necessary, but the logos should be on there is some format.

Our creative minds on this are stretched, so we are looking for someone to make this their own, and show us what a good business card should look like.

We may like to get these printed with spot gloss, so keep that in mind with your designs.

www.fenathletics.co.uk

Industry/Entity Type

Business

Contact Information for Business Card

Leo Pemberton-Hale
Operations Manager
(+44) 1632 960 418
Leo@fenathletics.co.uk
www.fenathletics.co.uk

Font styles to use
Sans Serif
Other font styles liked:
• Eurostile

Colors
ffffff

Requirements
Nice to have
• Dark (black) background

```html
<!DOCTYPE html>
<html lang="en">
<head>
<meta charset="utf-8">
<title>Fen Athletics – Business Card</title>
<link href="https://fonts.googleapis.com/css2?family=Open+Sans:wght@400;600;700&display=swap" rel="stylesheet">
<style>
  :root {
    --stage: #3a3532;
    --card: #0e0e0e;
    --white: #ffffff;
    --red: #e0212b;
    --muted: #9a9a9a;
    --plum: #6b5673;
    --divider: #5a1216;
  }
  * { margin: 0; padding: 0; box-sizing: border-box; }
  html, body { width: 1200px; height: 900px; overflow: hidden; }
  body {
    background: var(--stage);
    font-family: "Open Sans", Arial, sans-serif;
    position: relative;
  }
  .card {
    position: absolute;
    top: 290px;
    width: 520px;
    height: 320px;
    background: var(--card);
    box-shadow: 0 10px 30px rgba(0,0,0,0.45);
  }
  .card--contact { left: 50px; }
  .card--brands { left: 630px; }

  /* contact side */
  .contact-wordmark {
    position: absolute;
    left: 60px;
    top: 160px;
    font-weight: 700;
    font-size: 64px;
    color: var(--white);
    line-height: 1;
  }
  .contact-divider {
    position: absolute;
    left: 290px;
    top: 60px;
    width: 1px;
    height: 200px;
    background: var(--divider);
  }
  .contact-info {
    position: absolute;
    left: 310px;
    top: 70px;
    color: var(--white);
  }
  .contact-name {
    color: var(--red);
    font-weight: 700;
    font-size: 17px;
    line-height: 1.2;
  }
  .contact-role { font-size: 13px; margin-bottom: 22px; }
  .contact-list { list-style: none; font-size: 12.5px; line-height: 1.55; }
  .contact-list li { display: flex; align-items: center; gap: 8px; }
  .contact-list svg { width: 10px; height: 10px; fill: var(--white); flex: none; }
  .contact-address { margin-top: 14px; font-size: 12.5px; line-height: 1.5; }

  /* brands side */
  .brand-lockup {
    position: absolute;
    left: 0; right: 0;
    top: 70px;
    text-align: center;
    color: var(--white);
  }
  .brand-lockup__name { font-weight: 700; font-size: 40px; line-height: 1; }
  .brand-lockup__tag {
    font-size: 10px;
    letter-spacing: 3px;
    color: var(--white);
    margin-top: 6px;
  }
  .brand-row {
    position: absolute;
    left: 0; right: 0;
    top: 200px;
    display: flex;
    justify-content: center;
    align-items: center;
    gap: 26px;
    font-weight: 600;
    font-size: 13px;
  }
  .brand-row__item--grit { color: var(--red); }
  .brand-row__item--elm { color: var(--muted); }
  .brand-row__item--tava { color: var(--plum); }
  .brand-row__item--fen { color: var(--white); }
</style>
</head>
<body>

<section class="card card--contact">
  <div class="contact-wordmark">Fen</div>
  <div class="contact-divider"></div>
  <div class="contact-info">
    <p class="contact-name">Owen Ashdale</p>
    <p class="contact-role">Managing Director</p>
    <ul class="contact-list">
      <li>
        <svg viewBox="0 0 10 10" aria-hidden="true"><path d="M2 0h2l1 3-1.5 1a6 6 0 0 0 2.5 2.5L7 5l3 1v2c0 1-1 2-2 2A8 8 0 0 1 0 2c0-1 1-2 2-2z"/></svg>
        +44(0)1632 960418
      </li>
      <li>
        <svg viewBox="0 0 10 10" aria-hidden="true"><path d="M0 2h10v6H0z M0 2l5 3.5L10 2" fill="none" stroke="#fff" stroke-width="1.2"/></svg>
        owen@fenathletics.co.uk
      </li>
      <li>
        <svg viewBox="0 0 10 10" aria-hidden="true"><circle cx="5" cy="5" r="5"/></svg>
        www.fenathletics.co.uk
      </li>
    </ul>
    <p class="contact-address">Linden Park, Hollowby,<br>Marsh, YO9 4ZZ</p>
  </div>
</section>

<section class="card card--brands">
  <div class="brand-lockup">
    <p class="brand-lockup__name">Fen Athletics</p>
    <p class="brand-lockup__tag">PERFORMANCE WEAR</p>
  </div>
  <div class="brand-row">
    <span class="brand-row__item brand-row__item--grit">Grit and Rain</span>
    <span class="brand-row__item brand-row__item--elm">ElmStretch</span>
    <span class="brand-row__item brand-row__item--tava">TavaPuni</span>
    <span class="brand-row__item brand-row__item--fen">Fen</span>
  </div>
</section>

</body>
</html>
```